Now Leasing Banner

Looking for a banner that says the following information approx 4' x 30'

Now Leasing Maplebrook Terrace 925-318-6042

Target Market(s)

Drive by traffic

Industry/Entity Type

Residential property management

Requirements
Must have
• Clear and readable from a distance

```html
<!DOCTYPE html>
<html lang="en">
<head>
<meta charset="utf-8">
<title>Now Leasing Banner – Maplebrook Terrace</title>
<link rel="stylesheet" href="https://fonts.googleapis.com/css2?family=Arimo:wght@700&display=swap">
<style>
  :root {
    --page-bg: #d9d9d9;
    --banner-bg: #ffffff;
    --red-top: #e3121e;
    --red-bottom: #9c0010;
  }
  html, body {
    margin: 0;
    padding: 0;
    width: 1200px;
    height: 900px;
    overflow: hidden;
    background: var(--page-bg);
  }
  .canvas {
    position: relative;
    width: 1200px;
    height: 900px;
    background: var(--page-bg);
  }
  .banner {
    position: absolute;
    left: 40px;
    top: 308px;
    width: 1120px;
    height: 284px;
    background: var(--banner-bg);
    box-shadow: 0 6px 14px rgba(0, 0, 0, 0.18);
  }
  .banner-art {
    display: block;
    width: 1120px;
    height: 284px;
  }
  .banner-text {
    font-family: "Arimo", Arial, sans-serif;
    font-weight: 700;
  }
</style>
</head>
<body>
<div class="canvas">
  <div class="banner">
    <svg class="banner-art" viewBox="0 0 1120 284" xmlns="http://www.w3.org/2000/svg">
      <defs>
        <linearGradient id="red-fill" x1="0" y1="0" x2="0" y2="1">
          <stop offset="0" stop-color="var(--red-top)"/>
          <stop offset="1" stop-color="var(--red-bottom)"/>
        </linearGradient>
        <filter id="soft-shadow" x="-5%" y="-5%" width="110%" height="120%">
          <feDropShadow dx="2" dy="4" stdDeviation="3" flood-color="#000" flood-opacity="0.28"/>
        </filter>
      </defs>
      <g class="banner-text" fill="url(#red-fill)" filter="url(#soft-shadow)">
        <text class="headline-now" transform="translate(49 253) rotate(-90)" x="0" y="0"
              font-size="44" textLength="216" lengthAdjust="spacingAndGlyphs">NOW</text>
        <text class="headline-leasing" x="65" y="262"
              font-size="314" textLength="515" lengthAdjust="spacingAndGlyphs">LEASING</text>
        <text class="property-name" x="602" y="139"
              font-size="130" textLength="499" lengthAdjust="spacingAndGlyphs">Maplebrook Terrace</text>
        <text class="property-phone" x="602" y="253"
              font-size="130" textLength="499" lengthAdjust="spacingAndGlyphs">925-318-6042</text>
      </g>
    </svg>
  </div>
</div>
</body>
</html>
```